Label Design for Food Brand

We want a modern label for our spice blends. We are completely open in which direction, it should be modern and beautiful.

Use for Sample spice mixture: "Kelvo Dusk"

Here the Packaging:
https://www.merlitrove-example.com/media/xlarge/1700_1.jpg
Abmessung: Ø 54 x 67 mm

Target Market(s)

Food

Industry/Entity Type

Food

Requirements
Must have
• Logo, Name of Flavr
Should not have
• Images of food

```html
<!DOCTYPE html>
<html lang="en">
<head>
<meta charset="UTF-8">
<title>Merlifare – BBQ Spicy Pepper Label</title>
<link href="https://fonts.googleapis.com/css2?family=Mulish:wght@300;400;800&display=swap" rel="stylesheet">
<style>
  :root {
    --page-bg: #ffffff;
    --label-dark: #1c1c1c;
    --label-mid: #3a3a3a;
    --ink-light: #ffffff;
    --band: #f2f2f2;
    --band-ink: #141414;
    --rule: #d9d9d9;
  }
  * { margin: 0; padding: 0; box-sizing: border-box; }
  html, body {
    width: 1200px;
    height: 750px;
    overflow: hidden;
    background: var(--page-bg);
  }
  .canvas {
    position: relative;
    width: 1200px;
    height: 750px;
    font-family: "Mulish", sans-serif;
  }
  .label {
    position: absolute;
    left: 220px;
    top: 95px;
    width: 760px;
    height: 560px;
    border-radius: 6px;
    background: radial-gradient(ellipse at 55% 35%, var(--label-mid) 0%, var(--label-dark) 75%);
    color: var(--ink-light);
    overflow: hidden;
  }
  .brand-band {
    position: absolute;
    left: 40px;
    top: 60px;
    width: 72px;
    height: 440px;
    background: var(--band);
  }
  .brand-name {
    position: absolute;
    left: 50%;
    top: 50%;
    transform: translate(-50%, -50%) rotate(-90deg);
    white-space: nowrap;
    font-size: 46px;
    font-weight: 800;
    letter-spacing: 2px;
    color: var(--band-ink);
  }
  .product-type {
    position: absolute;
    left: 140px;
    top: 40px;
    font-size: 210px;
    font-weight: 300;
    line-height: 1;
    letter-spacing: -4px;
  }
  .product-flavour {
    position: absolute;
    left: 146px;
    top: 262px;
    font-size: 64px;
    font-weight: 800;
    line-height: 1;
    letter-spacing: 1px;
  }
  .tagline {
    position: absolute;
    left: 146px;
    top: 362px;
    font-size: 30px;
    line-height: 1.1;
    letter-spacing: 0.5px;
  }
  .tagline .light { font-weight: 300; }
  .tagline .strong { font-weight: 800; }
  .claims {
    position: absolute;
    left: 146px;
    top: 440px;
    width: 574px;
    height: 80px;
  }
  .claims svg { position: absolute; left: 0; top: 0; }
  .claim {
    position: absolute;
    top: 34px;
    font-size: 22px;
    letter-spacing: 0.5px;
    font-weight: 300;
  }
  .claim b { font-weight: 800; }
  .claim-gluten { left: 8px; }
  .claim-msg { left: 232px; }
  .claim-soy { left: 422px; }
</style>
</head>
<body>
<div class="canvas">
  <div class="label">
    <div class="brand-band">
      <span class="brand-name">MERLIFARE</span>
    </div>

    <div class="product-type">BBQ</div>
    <div class="product-flavour">SPICY PEPPER</div>

    <div class="tagline">
      <span class="light">HANDCRAFTED WITH</span> <span class="strong">HIGHEST</span><br>
      <span class="strong">QUALITY INGREDIENTS</span>
    </div>

    <div class="claims">
      <svg width="574" height="80" viewBox="0 0 574 80" aria-hidden="true">
        <line x1="0" y1="2" x2="574" y2="2" stroke="#d9d9d9" stroke-width="3"/>
        <line x1="212" y1="2" x2="212" y2="70" stroke="#d9d9d9" stroke-width="4"/>
        <line x1="400" y1="2" x2="400" y2="70" stroke="#d9d9d9" stroke-width="4"/>
      </svg>
      <span class="claim claim-gluten">GLUTEN <b>FREE</b></span>
      <span class="claim claim-msg">NO <b>MSG</b></span>
      <span class="claim claim-soy">NO <b>SOY</b></span>
    </div>
  </div>
</div>
</body>
</html>
```